I need a SEO-friendly Wordpress website (making sure to style H1, H2, H3, etc correctly) for a Hawaii-based law firm called Meridian Crest Legal Group. Comparable websites include https://brvlaw.example/ and https://www.lomrit.example/ for design reference. The current copy on the TarnAdvocate.example website can be used.

```html
<!DOCTYPE html>
<html lang="en">
<head>
<meta charset="utf-8">
<title>Meridian Crest Legal Group</title>
<link href="https://fonts.googleapis.com/css2?family=Tinos:wght@400;700&family=Montserrat:wght@400;500&family=Oswald:wght@500;600&display=swap" rel="stylesheet">
<style>
:root{
  --orange:#b35f10;
  --rust:#8b3207;
  --rust-dark:#7d2b06;
  --accent-text:#a84e0c;
  --cream:#fbe6d1;
  --ink:#111;
  --body:#555;
  --white:#fff;
}
*{margin:0;padding:0;box-sizing:border-box}
html,body{width:1200px;height:2812px;overflow:hidden}
body{font-family:'Montserrat',sans-serif;color:var(--ink);background:var(--white);position:relative}
.serif{font-family:'Tinos',serif}
.topbar{position:absolute;left:0;top:0;width:1200px;height:41px;background:var(--orange);color:var(--white)}
.topbar .label{position:absolute;right:292px;top:11px;font-size:14px}
.topbar .icon-box{position:absolute;left:923px;top:0;width:42px;height:41px;background:#8f4a0a;display:flex;align-items:center;justify-content:center}
.topbar .phone{position:absolute;left:976px;top:8px;font-family:'Tinos',serif;font-size:21px;font-weight:700}
.header{position:absolute;top:41px;left:0;width:1200px;height:95px;background:var(--white)}
.brand{position:absolute;left:76px;top:24px;font-family:'Tinos',serif;font-weight:700;font-size:36px}
.nav{position:absolute;right:79px;top:39px;display:flex;gap:33px;font-size:14.5px;color:#333}
.nav .active{color:var(--orange)}
.hero{position:absolute;top:136px;left:0;width:1200px;height:541px;background:linear-gradient(100deg,#4a3a30 0%,#6b5647 35%,#7a6a5c 60%,#5a4a3c 100%)}
.hero-inner{position:absolute;inset:0;background:rgba(0,0,0,.25);text-align:center;color:var(--white)}
.hero .kicker{position:absolute;top:145px;width:100%;font-size:19px}
.hero h1{position:absolute;top:182px;width:100%;font-family:'Oswald',sans-serif;font-weight:600;font-size:52px;line-height:62px;letter-spacing:.3px}
.hero .lede{position:absolute;top:324px;width:100%;font-size:19px}
.btn{position:absolute;display:flex;align-items:center;justify-content:center;background:var(--rust);color:var(--white);font-family:'Tinos',serif;font-weight:700;font-size:19px;letter-spacing:.5px}
.btn::after{content:"";position:absolute;left:6px;top:6px;right:-6px;bottom:-6px;border:1px solid var(--rust)}
.hero .btn{left:453px;top:373px;width:294px;height:55px;font-size:18px}
.hero .btn::after{left:-4px;top:-4px;right:-4px;bottom:-4px;border-color:#c56a14}
.about-photo{position:absolute;left:130px;top:700px;width:400px;height:524px;background:linear-gradient(180deg,#e8e2dc 0%,#3b4a72 45%,#1d2a4a 100%);border-radius:160px 160px 0 0}
.about h2{position:absolute;left:576px;top:736px;font-family:'Tinos',serif;font-weight:700;font-size:41px;line-height:48px}
.about h3{position:absolute;left:577px;top:846px;font-weight:500;font-size:17.5px;color:var(--accent-text)}
.about p{position:absolute;left:578px;width:520px;font-size:13px;line-height:27px;color:var(--body)}
.about .btn{left:580px;top:1097px;width:182px;height:56px}
.services{position:absolute;top:1224px;left:0;width:1200px;height:636px;background:var(--cream)}
.card{position:absolute;top:63px;width:334px;height:505px;background:var(--white);border:1px solid #eadfd4;text-align:center}
.card .media{height:229px;border-top:8px solid var(--orange)}
.card h3{margin-top:26px;font-family:'Tinos',serif;font-weight:700;font-size:21px;letter-spacing:.8px}
.card p{margin:16px auto 0;width:294px;font-size:13px;line-height:26px;color:var(--body)}
.card p strong{font-weight:500;color:#333}
.card .btn{top:417px;width:182px;height:55px}
.cta h2{position:absolute;top:1918px;width:1200px;text-align:center;font-family:'Tinos',serif;font-weight:700;font-size:42px;line-height:52px}
.cta .line{position:absolute;top:2054px;left:343px;display:flex;align-items:center;gap:20px;font-family:'Tinos',serif;font-weight:700;font-size:29px;color:var(--rust)}
.cta .circle{width:78px;height:76px;border-radius:50%;background:var(--rust);display:flex;align-items:center;justify-content:center;box-shadow:3px 3px 0 #fff,4px 4px 0 var(--rust)}
.map{position:absolute;top:2192px;left:0;width:1200px;height:390px;background:linear-gradient(135deg,#eeeeec,#e3e6e2 50%,#ececea)}
.contact-card{position:absolute;left:744px;top:2242px;width:338px;height:254px;background:var(--white);box-shadow:0 1px 4px rgba(0,0,0,.15)}
.contact-card h3{position:absolute;left:35px;top:30px;font-family:'Tinos',serif;font-weight:700;font-size:31px}
.contact-card .row{position:absolute;left:36px;display:flex;gap:16px;font-size:13px;line-height:27px;color:#333}
.contact-card .row svg{flex:none;width:24px}
.footer{position:absolute;top:2582px;left:0;width:1200px;height:230px;background:var(--rust-dark);color:var(--white);text-align:center}
.footer .ring{position:absolute;left:574px;top:44px;width:52px;height:52px;border:1px solid #c9701e;border-radius:50%;display:flex;align-items:center;justify-content:center}
.footer .name{position:absolute;top:114px;width:100%;font-family:'Tinos',serif;font-weight:700;font-size:36px}
.footer .legal{position:absolute;top:166px;width:100%;font-size:13px}
</style>
</head>
<body>
<div class="topbar">
  <span class="label">Call Us Today :</span>
  <div class="icon-box"><svg width="18" height="18" viewBox="0 0 24 24"><path fill="#fff" d="M6.6 10.8a15.1 15.1 0 0 0 6.6 6.6l2.2-2.2c.3-.3.7-.4 1-.2 1.1.4 2.3.6 3.6.6.6 0 1 .4 1 1V20c0 .6-.4 1-1 1C10.6 21 3 13.4 3 4c0-.6.4-1 1-1h3.5c.6 0 1 .4 1 1 0 1.3.2 2.5.6 3.6.1.3 0 .7-.2 1z"/></svg></div>
  <span class="phone">+1.808.555.0147</span>
</div>

<header class="header">
  <div class="brand">Meridian Crest Legal Group</div>
  <nav class="nav">
    <span class="active">HOME</span><span>PRACTIE AREAS</span><span>ATTORNEY</span><span>BLOG</span><span>CONTACT US</span>
  </nav>
</header>

<section class="hero" role="img" aria-label="Photo of parents arguing in the background while two children lean sadly on a table">
  <div class="hero-inner">
    <p class="kicker">Over 70 years of combined practice, specializing in:</p>
    <h1>Personal Injury Family &amp; Divorce<br>Child Custody</h1>
    <p class="lede">Dedicated to making sure you receive the care and attention you need.</p>
    <div class="btn">GET FREE CONSULTATION</div>
  </div>
</section>

<section class="about">
  <div class="about-photo" role="img" aria-label="Portrait of a senior attorney in a navy suit with arms crossed"></div>
  <h2>About The Kona<br>Lawyers Of MCLG</h2>
  <h3>Lawyers Serving the Big Island and Neighboring Islands</h3>
  <p style="top:893px">The experienced attorneys in the Meridian Crest Legal Group's Kailua Kona, Hawaii office provide clients with a wide range of litigation expertise, including legal claims involving divorce &amp; family, personal injury, toxic exposures, intellectual property, and real estate.</p>
  <p style="top:1018px">Our Kona office also offers commercial and hospitality litigation expertise on behalf of a wide variety of clients, including restaurants,...</p>
  <div class="btn">LEARN MORE</div>
</section>

<section class="services">
  <article class="card" style="left:77px">
    <div class="media" role="img" aria-label="Hand signing a legal document with a pen" style="background:linear-gradient(135deg,#8a9ab0,#d8dce2 45%,#7a5234)"></div>
    <h3>PRACTIE AREAS</h3>
    <p>The Big Island based attorneys of Tarn Advocate are licensed in several states, and specialize in numerous areas including divorce, family &amp; custody.</p>
    <div class="btn" style="left:71px">LEARN MORE</div>
  </article>
  <article class="card" style="left:434px">
    <div class="media" role="img" aria-label="Group of four attorneys standing in a city setting" style="background:linear-gradient(180deg,#b9b2a8,#4a4644 55%,#222)"></div>
    <h3>ATTORNEY</h3>
    <p>Our lawyers are board-certified specialists in all fields of our practice. With over 70 combined years experience, you're in good hands with us.</p>
    <div class="btn" style="left:72px">LEARN MORE</div>
  </article>
  <article class="card" style="left:790px">
    <div class="media" role="img" aria-label="Woman reading a book at a desk by a window" style="background:linear-gradient(120deg,#6b88a8,#e2b070 45%,#7a5a3c)"></div>
    <h3>BLOG</h3>
    <p><strong>Top 10 Things to Do Before Filing for Divorce</strong><br>No one gets married with the intention of things not working out, but it's.</p>
    <div class="btn" style="left:77px">LEARN MORE</div>
  </article>
</section>

<section class="cta">
  <h2>If You Have An Any Question For<br>Contact Us Today !</h2>
  <div class="line">
    <span>Call Us Today :</span>
    <div class="circle"><svg width="34" height="34" viewBox="0 0 24 24"><path fill="#fff" d="M6.6 10.8a15.1 15.1 0 0 0 6.6 6.6l2.2-2.2c.3-.3.7-.4 1-.2 1.1.4 2.3.6 3.6.6.6 0 1 .4 1 1V20c0 .6-.4 1-1 1C10.6 21 3 13.4 3 4c0-.6.4-1 1-1h3.5c.6 0 1 .4 1 1 0 1.3.2 2.5.6 3.6.1.3 0 .7-.2 1z"/></svg></div>
    <span>+1.808.555.0147</span>
  </div>
</section>

<div class="map" role="img" aria-label="Street map showing the office location"></div>
<aside class="contact-card">
  <h3>Contact Us</h3>
  <div class="row" style="top:88px"><svg height="32" viewBox="0 0 24 32"><path fill="#b35f10" d="M12 0C5.4 0 1 4.8 1 10.5 1 18 12 32 12 32s11-14 11-21.5C23 4.8 18.6 0 12 0zm0 15a4.5 4.5 0 1 1 0-9 4.5 4.5 0 0 1 0 9z"/></svg><span>48-210 Halewai Street, Suite 302<br>Hilo Bay, Hawaii 96720</span></div>
  <div class="row" style="top:160px"><svg height="22" viewBox="0 0 24 24"><path fill="#b35f10" d="M6.6 10.8a15.1 15.1 0 0 0 6.6 6.6l2.2-2.2c.3-.3.7-.4 1-.2 1.1.4 2.3.6 3.6.6.6 0 1 .4 1 1V20c0 .6-.4 1-1 1C10.6 21 3 13.4 3 4c0-.6.4-1 1-1h3.5c.6 0 1 .4 1 1 0 1.3.2 2.5.6 3.6.1.3 0 .7-.2 1z"/></svg><span>+1.808.555.0147</span></div>
  <div class="row" style="top:200px"><svg height="22" viewBox="0 0 24 24"><path fill="#b35f10" d="M2 5h20v3l-10 6L2 8zm0 5l10 6 10-6v9H2z"/></svg><span>clients@tarnadvocate.example</span></div>
</aside>

<footer class="footer">
  <div class="ring"><svg width="18" height="18" viewBox="0 0 24 24"><path fill="#c9701e" d="M2 5h20v3l-10 6L2 8zm0 5l10 6 10-6v9H2z"/></svg></div>
  <div class="name">Meridian Crest Legal Group</div>
  <p class="legal">©2019 Meridian Crest Legal Group. - All Rights Reserved. Privacy Policy &nbsp;| Tearms &amp; Condition</p>
</footer>
</body>
</html>
```